Professional Services - letterhead / business cards

The company (velmora partners) will provide services to Investment Funds and large investors in Spain. I have recently chosen a logo that I am attaching.

I would like a simple stationary design that i could use as letter head, business cards and "with compliments" cards.

I am not quite sure which color I will mostly use for the logo, in the email signature I will probably lean towards the white background and grey letters. I am attaching my favourite options.

Target Market(s)

Large Multinationals, Investment funds and Law firms

Industry/Entity Type

Business

Requirements
Must have
• my details are:
Luis R. Abadal
Velmora Partners S.L.
Casa de Torrelumbre
Calle de Vientoalto 27
28014 Madrid
T: +34 (91) 387-2265
M: +34 (646) 819-054
e-mail: labadal@velmorapartners.com

```html
<!DOCTYPE html>
<html lang="en">
<head>
<meta charset="utf-8">
<title>Velmora Partners – Business Card</title>
<link rel="stylesheet" href="https://fonts.googleapis.com/css2?family=Jost:ital,wght@0,400;0,500;1,400&display=swap">
<style>
  :root {
    --navy: #1d1f7a;
    --navy-deep: #15176a;
    --silver: #a9abb3;
    --ink-grey: #6a6c75;
    --paper: #ffffff;
    --backdrop: #e9e8e6;
    --on-navy: #f2f3fa;
  }
  * { margin: 0; padding: 0; box-sizing: border-box; }
  html, body { width: 1200px; height: 588px; overflow: hidden; }
  body {
    background: var(--backdrop);
    font-family: "Jost", "Century Gothic", sans-serif;
    position: relative;
  }
  .card {
    position: absolute;
    top: 144px;
    width: 500px;
    height: 300px;
    background: var(--paper);
    border-radius: 14px;
    overflow: hidden;
    box-shadow: 0 6px 18px rgba(0,0,0,0.18);
  }
  .card--front { left: 60px; }
  .card--back { left: 640px; }

  .wordmark {
    color: var(--navy);
    font-weight: 400;
    letter-spacing: 0.5px;
    white-space: nowrap;
  }
  .card--front .wordmark {
    position: absolute;
    top: 26px;
    right: 40px;
    font-size: 34px;
  }
  .holder {
    position: absolute;
    top: 92px;
    right: 70px;
    text-align: center;
    width: 300px;
  }
  .holder__name {
    color: var(--navy);
    font-size: 19px;
    letter-spacing: 1.5px;
    text-transform: uppercase;
  }
  .holder__company {
    color: var(--ink-grey);
    font-style: italic;
    font-size: 12px;
    margin-top: 2px;
  }
  .holder__email {
    color: var(--ink-grey);
    font-style: italic;
    font-size: 13px;
    margin-top: 4px;
  }
  .wave {
    position: absolute;
    left: 0;
    bottom: 0;
    width: 500px;
    height: 150px;
  }
  .contact {
    position: absolute;
    right: 30px;
    bottom: 14px;
    color: var(--on-navy);
    font-style: italic;
    font-size: 14px;
    text-align: right;
    line-height: 1.55;
  }
  .contact__line { display: flex; justify-content: flex-end; align-items: center; gap: 8px; }
  .contact__line svg { width: 12px; height: 12px; fill: var(--on-navy); }
  .contact__address { margin-top: 8px; font-size: 13.5px; }

  .card--back .wordmark {
    position: absolute;
    top: 98px;
    left: 0;
    width: 100%;
    text-align: center;
    font-size: 48px;
  }
  .card--back .website {
    position: absolute;
    top: 178px;
    left: 0;
    width: 100%;
    text-align: center;
    color: var(--navy);
    font-size: 14px;
    letter-spacing: 4px;
  }
</style>
</head>
<body>
  <section class="card card--front" aria-label="Business card front">
    <div class="wordmark">velmora partners</div>
    <div class="holder">
      <div class="holder__name">Luis R. Abadal</div>
      <div class="holder__company">Velmora Partners S.L.</div>
      <div class="holder__email">labadal@velmorapartners.com</div>
    </div>
    <svg class="wave" viewBox="0 0 500 150" preserveAspectRatio="none" aria-hidden="true">
      <path d="M0 20 C60 90 200 95 330 55 C400 35 460 28 500 30 L500 150 L0 150 Z" fill="var(--silver)"/>
      <path d="M0 26 C60 104 200 108 330 66 C400 44 460 36 500 38 L500 150 L0 150 Z" fill="var(--paper)"/>
      <path d="M0 32 C60 112 200 116 330 74 C400 52 460 44 500 46 L500 150 L0 150 Z" fill="var(--navy)"/>
      <path d="M0 44 C70 124 210 126 340 86 C410 64 465 58 500 60 L500 150 L0 150 Z" fill="var(--navy-deep)" opacity="0.5"/>
    </svg>
    <div class="contact">
      <div class="contact__line">
        <svg viewBox="0 0 24 24" aria-hidden="true"><path d="M6.6 10.8a15 15 0 0 0 6.6 6.6l2.2-2.2c.3-.3.7-.4 1-.2 1.1.4 2.3.6 3.6.6.6 0 1 .4 1 1V20c0 .6-.4 1-1 1A17 17 0 0 1 3 4c0-.6.4-1 1-1h3.5c.6 0 1 .4 1 1 0 1.3.2 2.5.6 3.6.1.3 0 .7-.2 1z"/></svg>
        <span>+34 (91) 387-2265</span>
      </div>
      <div class="contact__line">
        <svg viewBox="0 0 24 24" aria-hidden="true"><path d="M7 1h10a2 2 0 0 1 2 2v18a2 2 0 0 1-2 2H7a2 2 0 0 1-2-2V3a2 2 0 0 1 2-2zm0 4v13h10V5zm5 14.5a1 1 0 1 0 0 2 1 1 0 0 0 0-2z"/></svg>
        <span>+34 (646) 819-054</span>
      </div>
      <div class="contact__address">Casa de Torrelumbre, Calle de Vientoalto 27, 28014 Madrid</div>
    </div>
  </section>

  <section class="card card--back" aria-label="Business card back">
    <div class="wordmark">velmora partners</div>
    <div class="website">www.velmorapartners.com</div>
  </section>
</body>
</html>
```